Help Give House Painter “Fresh” Website Makeover!

A residential and commercial painting company based in Albuquerque, NM, USA needs a fresh, new, fun, and playful--yet, simple, elegant and professional--website made.

Here is a link to their existing site:

http://corvelcoatings.example/

We want to keep a similar site structure., So the navigation layout will stay the same. However, the video is too small, is too far over in the sidebar, and the overall design is amateur at best. We want something bright, colorful and bold!

We will need a space for the Video above the fold, and there needs to be space in the design for Testimonials, Specials and Images. It’s also very important to have the Pellham Roster awards that you see on his current website.

Please also include somewhere in the Design icons for YouTube, Facebook, Google+ and LinkedIn.

Here are some examples to look at to get your creative juices flowing!

http://brightloombrush.example/

http://www.tkvr.example/

http://www.marblow-tennick.example/

http://www.quarrypages.example/painting-company-niche-website/

http://www.brisklayoutdepot.example/website-templates/painting-company-website-template-53817.html

We have accounts at both lumavault.example and pixaroo.example. If you use placeholder images from there, that's fine. We can buy the images when and if your design is selected.

Target Market(s)

The audience is the average middle class homeowner to higher upper class. This should appeal to families, couples, and singles who own a home.

Industry/Entity Type

Residential

Font styles to use
Sans Serif

Requirements
Must have
• - - Lots of color! It's a site about painting homes. People like a variety of colors. Bring out your inner artist, and get bold with your colors!

- - A video place holder. As you can see, there is a video on the existing site, but it's small and hidden. Make it big and put it top left, or in the center.

- -Detailed and organized PSD structure. We're going to turn your design into a website, and to make that work soothly, we ask that you organize you PSD well: name your layers, keep things separated, group and ungroup as necessary, etc.

- A sidebar that goes down the right side of an interior page. We need a homepage, and also one [1] interior page template. We don't need you to make a design for each page. Just the homepage, followed by a simple interior page design that requires only the header/navigation, and a sidebar down the right side.
Should not have
• - Coding. This is a design project only.

```html
<!DOCTYPE html>
<html lang="en">
<head>
<meta charset="utf-8">
<title>Corvel Painting</title>
<link href="https://fonts.googleapis.com/css2?family=Lato:ital,wght@0,400;0,700;0,900;1,400;1,700&family=Ubuntu:wght@500;700&display=swap" rel="stylesheet">
<style>
:root{
  --navy:#13357a;
  --red:#e8141c;
  --blue:#0a74c4;
  --blue-dark:#07579c;
  --sky:#d6e7f5;
  --ink:#333;
  --dark:#1b2638;
  --orange:#ff7a00;
  --gold:#d9a21b;
}
*{margin:0;padding:0;box-sizing:border-box}
html,body{width:686px;height:1200px;overflow:hidden}
body{font-family:'Lato',sans-serif;color:var(--ink);background:#fff;position:relative}
.site-header{position:absolute;left:0;top:0;width:686px;height:80px;background:#fff}
.brand{position:absolute;left:76px;top:18px;display:flex;align-items:center;gap:9px}
.brand-mark{width:46px;height:46px;border-radius:50%;background:var(--blue)}
.brand-name{font-weight:900;font-size:23px;color:var(--navy);line-height:1;margin-top:-10px}
.brand-tag{position:absolute;left:160px;top:49px;font-size:10px;letter-spacing:1.4px;color:#555;padding-left:0}
.award{position:absolute;top:13px;width:70px;text-align:center;font-size:6.5px;color:var(--navy)}
.award-shape{width:30px;height:44px;margin:0 auto 5px;background:linear-gradient(#f0c23e,#c98e12);border-radius:4px 4px 15px 15px;box-shadow:0 1px 2px rgba(0,0,0,.3)}
.award.ext{left:361px}.award.int{left:420px}
.estimate-btn{position:absolute;left:493px;top:15px;width:102px;height:24px;background:var(--navy);color:#fff;font-weight:900;font-size:10.5px;display:flex;align-items:center;justify-content:center;border-radius:2px;box-shadow:0 1px 2px rgba(0,0,0,.3)}
.phone{position:absolute;left:499px;top:50px;display:flex;align-items:center;gap:6px;color:var(--red);font-weight:700;font-size:12.5px}
.main-nav{position:absolute;left:0;top:80px;width:686px;height:27px;background:linear-gradient(#1c8ad8,var(--blue-dark))}
.main-nav ul{list-style:none;display:flex;padding-left:75px;height:100%;align-items:center}
.main-nav li{color:#fff;font-weight:700;font-size:8.4px;margin-right:10.5px;position:relative}
.main-nav li.active::after{content:"";position:absolute;left:0;right:0;bottom:-6px;height:2px;background:#fff}
.hero{position:absolute;left:0;top:107px;width:686px;height:326px;overflow:hidden;
  background:
    radial-gradient(ellipse 160px 190px at 150px 170px,rgba(255,255,255,.55),rgba(255,255,255,0) 70%),
    radial-gradient(ellipse 120px 60px at 80px 300px,rgba(40,70,120,.45),rgba(40,70,120,0) 70%),
    linear-gradient(90deg,#1553c2 0%,#2a78e0 35%,#3a8de8 58%,#4b95e6 64%,#dfe5f4 70%,#eef1f9 100%)}
.hero::before{content:"";position:absolute;left:0;top:0;width:60px;height:326px;background:linear-gradient(90deg,rgba(200,210,225,.7),rgba(200,210,225,0))}
.hero-title{position:absolute;right:90px;top:318px;text-align:right;font-family:'Ubuntu',sans-serif;font-weight:700;font-size:30px;line-height:36px;color:var(--red);text-shadow:0 0 2px #fff,0 0 2px #fff,1px 1px 0 #fff,-1px -1px 0 #fff,2px 2px 2px rgba(0,0,0,.3)}
.dots{position:absolute;left:547px;top:406px;display:flex;gap:3px}
.dots span{width:9px;height:9px;border-radius:50%;background:#fff;box-shadow:0 0 1px #888}
.dots span.on{background:var(--red)}
.welcome-band{position:absolute;left:0;top:433px;width:686px;height:212px;background:linear-gradient(#f2f7fc,#e3eef8 50%,#c9def1)}
.welcome-card{position:absolute;left:75px;top:26px;width:534px;height:153px;background:#fff;border-radius:3px;box-shadow:0 4px 8px rgba(0,0,0,.18)}
.video{position:absolute;left:6px;top:6px;width:214px;height:141px;background:
  radial-gradient(ellipse 50px 70px at 160px 60px,#3d4a5e,rgba(61,74,94,0) 75%),
  radial-gradient(ellipse 60px 60px at 60px 80px,#a48f6e,rgba(164,143,110,0) 75%),
  linear-gradient(160deg,#b9c7a9,#94a184 50%,#6c6a5c)}
.video-play{position:absolute;left:93px;top:56px;width:28px;height:19px;background:var(--red);border-radius:5px}
.video-play::after{content:"";position:absolute;left:11px;top:5px;border-left:8px solid #fff;border-top:4.5px solid transparent;border-bottom:4.5px solid transparent}
.video-bar{position:absolute;left:0;bottom:0;width:100%;height:20px;background:linear-gradient(#333,#111)}
.video-bar .play{position:absolute;left:9px;top:6px;border-left:7px solid #fff;border-top:4px solid transparent;border-bottom:4px solid transparent}
.video-bar .vol{position:absolute;left:26px;top:7px;width:6px;height:6px;background:#fff}
.video-bar .track{position:absolute;left:42px;top:8px;width:115px;height:4px;background:#4a4a4a;border-radius:2px}
.video-bar .track i{display:block;width:55px;height:4px;background:#2d8ed8;border-radius:2px}
.video-bar .full{position:absolute;right:8px;top:6px;width:8px;height:8px;border:1.5px solid #fff}
.welcome-text{position:absolute;left:241px;top:9px;width:286px}
.welcome-text h2{font-size:12.5px;font-weight:700;color:var(--navy);margin-bottom:7px}
.welcome-text h2 span{color:var(--red)}
.welcome-text p{font-size:7.5px;line-height:11.5px;color:#555;letter-spacing:.15px}
.social{display:flex;gap:6px;margin-top:7px}
.social span{width:16px;height:16px;border-radius:2px}
.feature-band{position:absolute;left:0;top:645px;width:686px;height:313px;background:radial-gradient(ellipse 420px 200px at 343px 150px,#2b3a55,#1b2638 70%,#141c2b)}
.feature{position:absolute;top:33px;width:158px;height:237px;color:#fff;text-align:center;box-shadow:0 4px 10px rgba(0,0,0,.45);border-radius:0 0 6px 6px}
.feature h3{font-size:11.5px;font-weight:700;line-height:15px;margin-top:10px}
.feature.orange{left:77px;background:linear-gradient(#ff7400,#ff9a1c)}
.feature.cyan{left:265px;background:linear-gradient(#2a8fd6,#43b8f0)}
.feature.green{left:449px;width:160px;background:linear-gradient(#3f9e0c,#8fc828)}
.feature .thumb{width:138px;height:87px;margin:9px auto 0;border:4px solid #fff;box-shadow:0 1px 3px rgba(0,0,0,.3)}
.feature p{font-size:7.5px;line-height:11.8px;margin:10px 9px 0;color:#1a1a1a}
.feature .more{display:block;font-size:7.4px;font-weight:700;margin-top:10px;color:#1a1a1a}
.field{width:137px;height:17px;margin:6px auto 0;background:#fff;border-radius:2px;font-size:6.2px;font-weight:700;color:#555;text-align:left;padding:5px 9px}
.field.msg{height:42px}
.submit{width:80px;height:17px;margin:14px auto 0;background:var(--red);color:#fff;font-weight:700;font-size:9px;line-height:17px}
.review-band{position:absolute;left:0;top:958px;width:686px;height:188px;background:linear-gradient(#f2f7fc,#d7e7f5 50%,#a9cbea)}
.review-band h2{text-align:center;font-size:16.5px;font-weight:700;color:var(--navy);margin-top:20px}
.review-band h2 span{color:var(--red)}
.review-sub{text-align:center;font-size:7.8px;color:#777;margin-top:3px}
.rule{position:absolute;left:205px;top:61px;width:276px;height:1px;background:#c8d4e0}
.stars{position:absolute;left:0;width:100%;top:55px;text-align:center;color:var(--gold);font-size:10px;letter-spacing:1px}
.stars span{background:#e8f1f9;padding:0 4px}
.quote{position:absolute;left:75px;top:78px;width:470px;height:58px;background:#fff;padding:7px 14px 0 30px;font-style:italic;font-size:7.2px;line-height:11.5px;color:#444;box-shadow:0 2px 4px rgba(0,0,0,.12)}
.quote::before{content:"\201C";position:absolute;left:10px;top:0;font-size:26px;line-height:26px;color:#bbb;font-style:normal;font-weight:900}
.avatar{position:absolute;left:533px;top:74px;width:66px;height:66px;border-radius:50%;border:3px solid #fff;background:linear-gradient(#d6e0ea,#8ea3b6);box-shadow:0 2px 4px rgba(0,0,0,.25)}
.reviewer{position:absolute;right:152px;top:145px;font-style:italic;font-weight:700;font-size:7px;color:#333}
.site-footer{position:absolute;left:0;top:1146px;width:686px;height:54px;background:var(--dark);color:#fff;text-align:center}
.site-footer nav{font-size:7.2px;font-weight:700;margin-top:18px}
.site-footer p{font-size:6.7px;margin-top:5px;color:#ddd}
</style>
</head>
<body>
<header class="site-header">
  <div class="brand"><span class="brand-mark"></span><span class="brand-name">CORVEL PAINTING</span></div>
  <div class="brand-tag">NOT JUST ANOTHER PAINTER</div>
  <div class="award ext"><div class="award-shape" role="img" aria-label="Pellham Roster award badge"></div>Exterior Painting</div>
  <div class="award int"><div class="award-shape" role="img" aria-label="Pellham Roster award badge"></div>Interior Painting</div>
  <div class="estimate-btn">FREE ESTIMATES</div>
  <div class="phone">
    <svg width="14" height="14" viewBox="0 0 14 14"><circle cx="7" cy="7" r="6.2" fill="none" stroke="#111" stroke-width="1.3"/><path d="M4.6 3.8l1.3 1.4-.7 1c.5 1 1.2 1.7 2.2 2.2l1-.7 1.4 1.3-.8 1.1C6.6 10 4 7.4 3.9 4.6z" fill="#111"/></svg>
    123 456 7890
  </div>
</header>
<nav class="main-nav">
  <ul>
    <li class="active">HOME</li><li>ABOUT US</li><li>RESIDENTIAL PAINTING</li><li>COMMERCIAL PAINTING</li><li>FAQ</li><li>SPECIALS</li><li>BLOG</li><li>TESTIMONIALS</li><li>CONTACT US</li>
  </ul>
</nav>
<section class="hero" role="img" aria-label="Smiling painter on a ladder rolling blue paint onto a wall"></section>
<h1 class="hero-title">Residential &amp; Commercial<br>Painting Company</h1>
<div class="dots"><span></span><span class="on"></span><span></span><span></span></div>
<section class="welcome-band">
  <div class="welcome-card">
    <div class="video" role="img" aria-label="Video still of two people painting a room">
      <span class="video-play"></span>
      <div class="video-bar"><span class="play"></span><span class="vol"></span><div class="track"><i></i></div><span class="full"></span></div>
    </div>
    <div class="welcome-text">
      <h2>Welcome To CORVEL <span>PAINTING</span></h2>
      <p>Corvel Painting does jobs as small as a bathroom up to large commercial projects right here in Albuquerque and Rio Rancho. Extensive as an entire apartment exterior, to a kitchen and all home interior, no job is too big or too small for Corvel Painting of Albuquerque. Corvel Painting is staffed with the best painters for the highest quality paint jobs. Corvel Painting is not a community's average house painter staffing company, but this painting company is staffed with professional painters that pride themselves on successfully completing every job.</p>
      <div class="social"><span style="background:#3b5998" role="img" aria-label="Social link"></span><span style="background:#4fb6e8" role="img" aria-label="Social link"></span></div>
    </div>
  </div>
</section>
<section class="feature-band">
  <div class="feature orange">
    <h3>Our Painting<br>In Albuquerque</h3>
    <div class="thumb" role="img" aria-label="Couple painting a wall green" style="background:radial-gradient(ellipse 40px 50px at 40px 55px,#c98f86,rgba(201,143,134,0) 75%),linear-gradient(90deg,#f1ece2,#d8e3b0 60%,#b9d46c)"></div>
    <p>Corvel Painting does jobs as small as a bathroom up to large commercial projects right here in Albuquerque.</p>
    <span class="more">Read More &#187;</span>
  </div>
  <div class="feature cyan">
    <h3>Albuquerque<br>Painter Videos</h3>
    <div class="thumb" role="img" aria-label="Hand with a paint roller on an orange wall" style="background:radial-gradient(ellipse 60px 40px at 70px 35px,#f6c877,rgba(246,200,119,0) 75%),linear-gradient(#eba741,#d9862a)"></div>
    <p>TWe have shot a ton of videos with Rudy answering all of your most frequently asked questions. We want</p>
    <span class="more">Read More &#187;</span>
  </div>
  <div class="feature green">
    <h3>Free<br>Estimates</h3>
    <div class="field" style="margin-top:7px">Full Name</div>
    <div class="field">Email Address</div>
    <div class="field">Phone Number</div>
    <div class="field msg">Message</div>
    <div class="submit">SUBMIT</div>
  </div>
</section>
<section class="review-band">
  <h2>Our Customer <span>Review</span></h2>
  <p class="review-sub">Lorem ipsum dolor sit amet, consectetur Donec a consequat mag Aenean eu velit Aenean sollicitudin</p>
  <div class="rule"></div>
  <div class="stars"><span>&#9733;&#9733;&#9733;</span></div>
  <div class="quote">Lorem sum dolor sit amet, consectetuer adipiscing elit, sed diam nonummy nibh euismod tincidunt ut laoreet re agn aliqam erat volutpat wisi enim ad minim veniam, quis nostrud exerci tation ullamcorper suscipit lobortis nisl ut aliquip modo conseuatis autem vel eum iriure dolor in hendrerit in vulputate velit esse molestie consequat, vel illum dolore eu.</div>
  <div class="avatar" role="img" aria-label="Portrait of the reviewer"></div>
  <div class="reviewer">Meran, Tollbridge Works , USA</div>
</section>
<footer class="site-footer">
  <nav>HOME &nbsp;|&nbsp; ABOUT US &nbsp;|&nbsp; RESIDENTIAL PAINTING &nbsp;|&nbsp; COMMERCIAL PAINTING &nbsp;|&nbsp; FAQ &nbsp;|&nbsp; SPECIALS &nbsp;|&nbsp; BLOG &nbsp;|&nbsp; TESTIMONIALS &nbsp;|&nbsp; CONTACT US</nav>
  <p>&copy; 2015 CORVEL PAINTING. ALL RIGHT RESERVED.</p>
</footer>
</body>
</html>
```